Business Cards for a law firm

Business cards for our law firm. Use our silhoette logo and OAK PARTNERS - check our website (www.oakpartners.example)

Contact Information for Business Card

our silhouette logo, OAK PARTNERS, 800-555-0147, Dorian Pemberton, dorian@oakpartners.example

Requirements
Must have
• our silhouette logo, OAK PARTNERS, 800-555-0147, Dorian Pemberton, dorian@oakpartners.example

```html
<!DOCTYPE html>
<html lang="en">
<head>
<meta charset="utf-8">
<title>Oak Partners – Business Cards</title>
<link rel="stylesheet" href="https://fonts.googleapis.com/css2?family=Montserrat:wght@400;500;600;700&display=swap">
<style>
  :root {
    --navy: #22336b;
    --navy-edge: #1b2a5c;
    --white: #ffffff;
    --ink: #1f1f24;
    --backdrop: #c4c4c4;
    --shadow: rgba(0, 0, 0, 0.28);
  }
  * { box-sizing: border-box; margin: 0; padding: 0; }
  html, body {
    width: 1200px;
    height: 815px;
    overflow: hidden;
  }
  body {
    background: linear-gradient(180deg, #cfcfcf 0%, var(--backdrop) 55%, #a9a9a9 100%);
    font-family: "Montserrat", sans-serif;
    display: flex;
    align-items: center;
    justify-content: center;
    gap: 40px;
  }
  .card {
    position: relative;
    width: 540px;
    height: 308px;
    border-radius: 22px;
    box-shadow: 0 14px 30px var(--shadow);
    overflow: hidden;
  }
  /* Front */
  .card-front {
    background: var(--white);
    border-bottom: 4px solid var(--navy-edge);
    color: var(--navy);
  }
  .front-brand {
    position: absolute;
    top: 62px;
    left: 0;
    right: 0;
    display: flex;
    align-items: center;
    justify-content: center;
    gap: 12px;
    padding-left: 90px;
  }
  .brand-dot {
    width: 22px;
    height: 22px;
    border-radius: 50%;
    background: var(--navy);
  }
  .brand-name {
    font-weight: 600;
    font-size: 30px;
    letter-spacing: 2px;
    color: var(--navy);
  }
  .holder {
    position: absolute;
    left: 36px;
    top: 158px;
  }
  .holder-name {
    font-weight: 700;
    font-size: 21px;
    letter-spacing: 0.5px;
    text-transform: uppercase;
    color: var(--navy);
  }
  .holder-role {
    font-weight: 400;
    font-size: 12px;
    letter-spacing: 0.5px;
    color: var(--ink);
    margin-top: 2px;
  }
  .divider {
    position: absolute;
    left: 36px;
    right: 36px;
    top: 208px;
    height: 1.5px;
    background: var(--navy);
  }
  .contact-list {
    position: absolute;
    left: 44px;
    top: 222px;
    list-style: none;
  }
  .contact-list li {
    display: flex;
    align-items: center;
    gap: 10px;
    font-size: 13px;
    color: var(--ink);
    line-height: 22px;
  }
  .contact-list svg { width: 12px; height: 12px; flex: none; }
  .address {
    position: absolute;
    right: 36px;
    top: 224px;
    text-align: right;
    font-style: normal;
    font-size: 12.5px;
    line-height: 18px;
    color: var(--ink);
  }
  /* Back */
  .card-back {
    background: var(--navy);
    display: flex;
    align-items: center;
    justify-content: center;
    gap: 18px;
  }
  .card-back .brand-dot {
    width: 34px;
    height: 34px;
    background: var(--white);
  }
  .card-back .brand-name {
    font-size: 44px;
    letter-spacing: 3px;
    color: var(--white);
  }
</style>
</head>
<body>
  <section class="card card-front" aria-label="Business card front">
    <div class="front-brand">
      <span class="brand-dot"></span>
      <span class="brand-name">OAK PARTNERS</span>
    </div>
    <div class="holder">
      <p class="holder-name">Dorian Pemberton</p>
      <p class="holder-role">OWNER</p>
    </div>
    <div class="divider"></div>
    <ul class="contact-list">
      <li>
        <svg viewBox="0 0 12 12" aria-hidden="true"><path d="M2.5 1 L4.5 1 L5.3 3.6 L4 4.6 C4.6 6 6 7.4 7.4 8 L8.4 6.7 L11 7.5 L11 9.5 C11 10.3 10.3 11 9.5 11 C5 11 1 7 1 2.5 C1 1.7 1.7 1 2.5 1 Z" fill="var(--navy)"/></svg>
        800-555-0147
      </li>
      <li>
        <svg viewBox="0 0 12 12" aria-hidden="true"><rect x="0.5" y="2" width="11" height="8" rx="1" fill="var(--navy)"/><path d="M1 2.6 L6 6.6 L11 2.6" stroke="#fff" stroke-width="1" fill="none"/></svg>
        dorian@oakpartners.example
      </li>
      <li>
        <svg viewBox="0 0 12 12" aria-hidden="true"><circle cx="6" cy="6" r="5.2" fill="var(--navy)"/><ellipse cx="6" cy="6" rx="2.2" ry="5.2" stroke="#fff" stroke-width="0.8" fill="none"/><line x1="0.8" y1="6" x2="11.2" y2="6" stroke="#fff" stroke-width="0.8"/></svg>
        www.oakpartners.example
      </li>
    </ul>
    <address class="address">1420 Harbor Lane #310,<br>Fairview, CA 90000</address>
  </section>

  <section class="card card-back" aria-label="Business card back">
    <span class="brand-dot"></span>
    <span class="brand-name">OAK PARTNERS</span>
  </section>
</body>
</html>
```